Coastal Learner Bureau business cards

Australian company about to start offering its services. We recruit international students to come to study English, vocational education and postgraduate courses in Australia. We help them find the institution and select the right city they want to come to Australia. We are a young, online oriented and supportive agency. Our clients are between 18 and 35 years old, mainly University students, young professionals or people with work experience. We provide much more information that any other agency offer. We administrate a Facebook group with more than 11.000 members that daily ask questions about general information when coming to Australia, while they are here and even after they leave the country

Target Market(s)

International students from South America, Central America and Europe

Industry/Entity Type

Student

Contact Information for Business Card

Tomas Bilbrea
Managing Director
tomas@kelvarin.com.au
www.kelvoria.com.au
+61 491058264
Melbourne, Australia

Font styles to use
Serif
Sans Serif

Colors

Designer to choose colors to be used in the design.

Requirements
Must have
• Horizontal design
• Standard business card size and shape. If font uses green or yellow colours, they will have to match the ones from the logo
Nice to have
• UPDATE: Use the contents of the green image to design one of the card sides. Use our logo in the background of that side as watermark.
• Passport image, or immigration stamps. A picture of the Yarra River (from Melbourne) would be cool as well.
Should not have
• Non-standard business card size and shape
• Not black as the background colour of any sides as we are not a VIP agency or a hight class service. We are orientes to young people and they like colours, pictures, something attractive.
• Vertical design
• NO YELLOW or BLACK AS THE BACKGROUND COLOUR OF ANY SIDE OF THE BIZ CARD

```html
<!DOCTYPE html>
<html lang="en">
<head>
<meta charset="utf-8">
<title>Coastal Learner Bureau business cards</title>
<link rel="stylesheet" href="https://fonts.googleapis.com/css2?family=Open+Sans:wght@400;600;700&family=Tinos:wght@700&display=swap">
<style>
  :root {
    --stage: #ebe8e4;
    --card-white: #ffffff;
    --brand-green: #1a5e3c;
    --brand-green-soft: #21694a;
    --brand-yellow: #e6bf1c;
    --ink: #2a2a2a;
  }
  * { box-sizing: border-box; margin: 0; padding: 0; }
  html, body {
    width: 1200px; height: 900px; overflow: hidden;
    background: var(--stage);
    font-family: "Open Sans", Arial, sans-serif;
  }
  .canvas { position: relative; width: 1200px; height: 900px; }

  .card { position: absolute; box-shadow: 0 6px 18px rgba(0,0,0,.18); }

  /* Front side */
  .card-front {
    left: 78px; top: 35px; width: 587px; height: 362px;
    background: var(--card-white);
  }
  .accent-bar { position: absolute; left: 0; width: 17px; }
  .accent-bar--green { top: 37px; height: 41px; background: var(--brand-green); }
  .accent-bar--yellow { top: 273px; height: 58px; background: var(--brand-yellow); }

  .holder { position: absolute; left: 32px; top: 36px; }
  .holder-name {
    font-size: 18px; font-weight: 700; letter-spacing: .2px;
    color: var(--brand-green); line-height: 1.2;
  }
  .holder-name .first { color: var(--brand-yellow); }
  .holder-title { font-size: 15px; color: var(--ink); line-height: 1.3; }

  .brand-front {
    position: absolute; left: 318px; top: 118px; width: 240px;
    display: flex; align-items: center; gap: 10px;
  }
  .brand-dot { width: 18px; height: 18px; border-radius: 50%; background: var(--brand-yellow); flex: none; }
  .brand-name {
    font-size: 48px; font-weight: 700; color: var(--brand-green); line-height: 1;
  }

  .contact-list { position: absolute; left: 33px; top: 268px; list-style: none; }
  .contact-list li {
    display: flex; align-items: center; gap: 8px;
    font-size: 15.5px; color: var(--ink); height: 21px;
  }
  .contact-list svg { width: 11px; height: 11px; flex: none; }

  .location {
    position: absolute; right: 36px; top: 310px;
    font-size: 15.5px; color: var(--ink);
  }

  /* Back side */
  .card-back {
    left: 388px; top: 505px; width: 567px; height: 352px;
    background: var(--brand-green);
    overflow: hidden;
  }
  .watermark-field {
    position: absolute; inset: 0;
    background: linear-gradient(180deg, var(--brand-green-soft), var(--brand-green));
  }
  .brand-back {
    position: absolute; left: 0; right: 0; top: 135px;
    display: flex; justify-content: center; align-items: center; gap: 10px;
  }
  .brand-back .brand-name { color: var(--card-white); font-size: 54px; }
  .tagline {
    position: absolute; left: 0; right: 0; top: 290px; text-align: center;
    font-family: "Tinos", "Times New Roman", serif; font-weight: 700;
    font-size: 19px; color: var(--brand-yellow); letter-spacing: .3px;
  }
</style>
</head>
<body>
<main class="canvas">

  <section class="card card-front" aria-label="Business card front">
    <span class="accent-bar accent-bar--green"></span>
    <div class="holder">
      <p class="holder-name"><span class="first">TOMAS</span> BILBREA</p>
      <p class="holder-title">Managing Director</p>
    </div>

    <div class="brand-front">
      <span class="brand-dot"></span>
      <span class="brand-name">Kelvoria</span>
    </div>

    <span class="accent-bar accent-bar--yellow"></span>
    <ul class="contact-list">
      <li>
        <svg viewBox="0 0 12 12" aria-hidden="true"><path fill="#1a5e3c" d="M2.4 0.6 4 0.2 5.2 3 4.1 4.1c.7 1.5 1.9 2.7 3.4 3.4L8.6 6.4 11.4 7.6 11 9.2C10.7 10.6 9.6 11.4 8.3 11.2 4.5 10.4 1.4 7.3.6 3.5.4 2.2 1.1 1 2.4.6Z"/></svg>
        <span>+61 491058264</span>
      </li>
      <li>
        <svg viewBox="0 0 12 12" aria-hidden="true"><rect x="0.5" y="2" width="11" height="8" fill="#1a5e3c"/><path d="M1 2.6 6 6.6 11 2.6" fill="none" stroke="#fff" stroke-width="1"/></svg>
        <span>tomas@kelvarin.com.au</span>
      </li>
      <li>
        <svg viewBox="0 0 12 12" aria-hidden="true"><g fill="none" stroke="#1a5e3c" stroke-width="1.2"><circle cx="6" cy="6" r="5"/><ellipse cx="6" cy="6" rx="2.2" ry="5"/><path d="M1 6h10"/></g></svg>
        <span>www.kelvoria.com.au</span>
      </li>
    </ul>
    <p class="location">Melbourne, Australia</p>
  </section>

  <section class="card card-back" aria-label="Business card back">
    <div class="watermark-field" role="img" aria-label="Faint repeated brand watermark pattern on green"></div>
    <div class="brand-back">
      <span class="brand-dot"></span>
      <span class="brand-name">Kelvoria</span>
    </div>
    <p class="tagline">HACEMOS MÁS POR TI!</p>
  </section>

</main>
</body>
</html>
```